Business card design Needed for new logo / Construction business, home extensions and new builds

We need a business card design using our new logo files which i will attach to this project :)

We are a small construction business specialising in home extensions, new builds and property development. We are very ambitious and would appreciate professional and elegant designs for our new business card.

Very serious about using the services on MakerQuarry and recently acquired our new logo from here :)

Please get involved, i will feedback when i can as i am very busy but can respond daily, thanks

Target Market(s)

People that want to build onto their houses, new building developments or adding too their existing property

Industry/Entity Type

Construction

Contact Information for Business Card

Renwick Tolliver Construction, Lionel Ashby (Managing Director), Tel 07822254961, email - info@renwick-tolliver, www.renwick-tolliver.co.uk

Colors

Designer to choose colors to be used in the design.

Requirements
Must have
• I like a deep grey on the back please. A lot of you have provided black from and back, try mixing things up a little. The black looks cool 😎 Thanks

```html
<!DOCTYPE html>
<html lang="en">
<head>
<meta charset="utf-8">
<title>Renwick Tolliver Construction – Business Card</title>
<link rel="stylesheet" href="https://fonts.googleapis.com/css2?family=Cinzel:wght@400;600&display=swap">
<style>
  :root {
    --backdrop: #b4b4b2;
    --deep-grey: #323232;
    --paper: #ffffff;
    --gold: #d4a02c;
    --gold-dark: #bd7f12;
    --gold-light: #fbd98c;
    --silver: #c9cacc;
    --silver-dark: #8e9093;
    --ink: #1e1e1e;
  }
  * { margin: 0; padding: 0; box-sizing: border-box; }
  html, body { width: 1200px; height: 850px; overflow: hidden; }
  body {
    background: var(--backdrop);
    position: relative;
    font-family: "Cinzel", "Times New Roman", serif;
  }
  .card {
    position: absolute;
    left: 324px;
    width: 553px;
    height: 331px;
    border-radius: 32px;
    overflow: hidden;
  }
  .card svg.card-art { position: absolute; inset: 0; width: 100%; height: 100%; }
  .card-front { top: 68px; background: var(--deep-grey); }
  .card-back { top: 451px; background: var(--paper); }

  /* front */
  .brand-mark {
    position: absolute;
    left: 246px; top: 92px;
    width: 60px; height: 60px;
    border-radius: 50%;
    background: var(--gold);
  }
  .brand-name {
    position: absolute;
    left: 0; right: 0;
    text-align: center;
    color: var(--gold);
    font-weight: 400;
    white-space: nowrap;
  }
  .brand-name-main { top: 190px; font-size: 24px; letter-spacing: 0.5px; }
  .brand-name-sub { top: 227px; font-size: 17px; letter-spacing: 1px; }
  .brand-rule {
    position: absolute;
    top: 241px;
    width: 26px;
    height: 2px;
    background: var(--gold);
  }
  .brand-rule-left { left: 162px; }
  .brand-rule-right { left: 365px; }

  /* back */
  .holder-name {
    position: absolute;
    left: 256px; top: 44px;
    font-size: 25px;
    font-weight: 400;
    color: var(--gold);
    letter-spacing: 0.5px;
  }
  .holder-role {
    position: absolute;
    left: 257px; top: 75px;
    font-size: 15px;
    color: var(--ink);
    letter-spacing: 0.5px;
  }
  .contact-list { list-style: none; position: absolute; left: 256px; top: 139px; }
  .contact-item {
    display: flex;
    align-items: center;
    height: 22px;
    font-size: 14px;
    color: var(--ink);
    letter-spacing: 0.5px;
    white-space: nowrap;
  }
  .contact-item + .contact-item { margin-top: 12.5px; }
  .contact-item:last-child { margin-top: 15px; }
  .contact-icon { width: 21px; height: 21px; margin-right: 10px; flex: none; }
</style>
</head>
<body>

<section class="card card-front" aria-label="Card front">
  <svg class="card-art" viewBox="0 0 553 331" aria-hidden="true">
    <defs>
      <linearGradient id="goldSheen" x1="0" y1="0" x2="1" y2="1">
        <stop offset="0" stop-color="#bd7f12"/>
        <stop offset="0.45" stop-color="#fbd98c"/>
        <stop offset="0.75" stop-color="#c58a1c"/>
        <stop offset="1" stop-color="#f2b53a"/>
      </linearGradient>
      <linearGradient id="silverSheen" x1="0" y1="0" x2="1" y2="1">
        <stop offset="0" stop-color="#8e9093"/>
        <stop offset="0.5" stop-color="#e6e7e8"/>
        <stop offset="1" stop-color="#8e9093"/>
      </linearGradient>
    </defs>
    <polygon points="0,0 46,0 98,55 0,246" fill="url(#silverSheen)"/>
    <polygon points="0,0 40,0 90,55 0,238" fill="url(#goldSheen)"/>
    <polygon points="553,74 460,262 525,331 553,331" fill="url(#silverSheen)"/>
    <polygon points="553,81 468,262 530,331 553,331" fill="url(#goldSheen)"/>
  </svg>
  <span class="brand-mark" aria-hidden="true"></span>
  <p class="brand-name brand-name-main">RENWICK TOLLIVER</p>
  <span class="brand-rule brand-rule-left" aria-hidden="true"></span>
  <p class="brand-name brand-name-sub">Construction</p>
  <span class="brand-rule brand-rule-right" aria-hidden="true"></span>
</section>

<section class="card card-back" aria-label="Card back">
  <svg class="card-art" viewBox="0 0 553 331" aria-hidden="true">
    <defs>
      <linearGradient id="goldSheenBack" x1="0" y1="0" x2="0.6" y2="1">
        <stop offset="0" stop-color="#bd7f12"/>
        <stop offset="0.45" stop-color="#fbd98c"/>
        <stop offset="0.78" stop-color="#c58a1c"/>
        <stop offset="1" stop-color="#f2b53a"/>
      </linearGradient>
      <linearGradient id="silverSheenBack" x1="0" y1="0" x2="0.6" y2="1">
        <stop offset="0" stop-color="#8e9093"/>
        <stop offset="0.5" stop-color="#e6e7e8"/>
        <stop offset="1" stop-color="#8e9093"/>
      </linearGradient>
    </defs>
    <polygon points="0,0 203,0 151,62 208,130 159,220 276,331 0,331" fill="var(--deep-grey)"/>
    <polygon points="0,0 107,0 202,130 105,331 0,331" fill="url(#silverSheenBack)"/>
    <polygon points="0,0 98,0 194,130 99,331 0,331" fill="url(#goldSheenBack)"/>
  </svg>

  <h1 class="holder-name">YOUR NAMER</h1>
  <p class="holder-role">Founder</p>

  <ul class="contact-list">
    <li class="contact-item">
      <svg class="contact-icon" viewBox="0 0 22 22" aria-hidden="true">
        <circle cx="11" cy="11" r="10.5" fill="var(--gold)"/>
        <path d="M11 5.5a3.6 3.6 0 0 0-3.6 3.6c0 2.7 3.6 6.6 3.6 6.6s3.6-3.9 3.6-6.6A3.6 3.6 0 0 0 11 5.5z" fill="#fff"/>
        <circle cx="11" cy="9.1" r="1.3" fill="var(--gold)"/>
      </svg>
      Your Adress
    </li>
    <li class="contact-item">
      <svg class="contact-icon" viewBox="0 0 22 22" aria-hidden="true">
        <circle cx="11" cy="11" r="10.5" fill="var(--gold)"/>
        <rect x="5.5" y="7.5" width="11" height="7.5" fill="#fff"/>
        <path d="M5.5 7.5 11 12l5.5-4.5M5.5 15l4-3.6M16.5 15l-4-3.6" fill="none" stroke="var(--gold)" stroke-width="0.8"/>
      </svg>
      Your email
    </li>
    <li class="contact-item">
      <svg class="contact-icon" viewBox="0 0 22 22" aria-hidden="true">
        <circle cx="11" cy="11" r="10.5" fill="var(--gold)"/>
        <g fill="none" stroke="#fff" stroke-width="0.9">
          <circle cx="11" cy="11" r="5.5"/>
          <ellipse cx="11" cy="11" rx="2.4" ry="5.5"/>
          <path d="M5.5 11h11M6.3 8.2h9.4M6.3 13.8h9.4"/>
        </g>
      </svg>
      Your website
    </li>
    <li class="contact-item">
      <svg class="contact-icon" viewBox="0 0 22 22" aria-hidden="true">
        <circle cx="11" cy="11" r="10.5" fill="var(--gold)"/>
        <path d="M7.6 5.8c.5-.4 1.1-.3 1.4.2l1 1.6c.3.5.2 1-.2 1.4l-.6.5c.5 1.2 1.5 2.3 2.7 2.9l.6-.6c.4-.4 1-.4 1.4-.1l1.6 1.1c.5.3.6 1 .2 1.4l-.8.9c-.5.5-1.3.7-2 .4-2.8-1.1-5-3.4-6-6.2-.3-.7 0-1.5.5-2z" fill="#fff"/>
      </svg>
      Your number telephone
    </li>
  </ul>
</section>

</body>
</html>
```